Web design for Crowdfunding site HopeWingsRally.com

We need a web design for christian crowdfunding website. Here is the challenge: We need responsive layout that is targeted first in iPad size of screen. It should also scale somehow down to iPhone size of screens. Web layout can be about the same size as iPad screen.

Screens should work so that main page scrolls not but only certain part of the screen scrolls and always one "page" at time. We can implement these "scrolls" then later with javascript but now we need only design. The challenge is to create this kind of hybrid website / app look.

Target is at first to raise funds to orphan people needing about $40 per month for their living and education. There is always some organization which takes care of these kids. Later there will be other christian missions included. At first we are looking to find monthly supporters.

You can be as creative as you want :) As you see from the look and feel sector, I am not looking any same traditional look which many "help kids" sites have. I am looking to reach now younger generation and therefore iPad and mobile are the main screen sizes.

Inspirational designs:
- https://example-gallery.test/profiles/studiofernlake/designs/482716?from=%2Fbrowse%2Fxhr%2Fdesigns%3Fcategory%3Dmobile-app-design
- http://www.artpoolhub.test/design/8261047 Clear, simple visuals
- http://www.artpoolhub.test/design/7394215 Header
- http://www.artpoolhub.test/design/6048392 Contrast in the colors, i think is powerfull

Some terms could be: Kids play, kids are learning (in the school). No static posture but living like kids are. I wonder also how we could also add little bit gaming style even though the question is of reali life of real people. Giving should be rewarding.

Target Market(s)

People who want help other people.

Industry/Entity Type

Christian

Number of Pages Required

4 page

Requirements
Must have
• Homepage. Mission page (In my wireframes it was one kid).
Nice to have
• Other pages and some idea how to scroll. 4 pages is no must. If you feel easy, please give first some draft and I give comments on that.

```html
<!DOCTYPE html>
<html lang="en">
<head>
<meta charset="utf-8">
<title>HopeWingsRally – Mission: Orphan Maria, 11y</title>
<link href="https://fonts.googleapis.com/css2?family=Montserrat:wght@400;500;600&family=Open+Sans:wght@400;600&display=swap" rel="stylesheet">
<style>
  :root{
    --black:#000;
    --white:#fff;
    --accent:#ffb400;
    --accent-dark:#e9a500;
    --tab-grey:#efefef;
    --tab-border:#d0d0d0;
    --text-body:#8a8a8a;
    --timeline:#c4c4c4;
    --icon-grey:#9a9a9a;
    --footer:#5b5b5b;
    --photo-a:#8f8e8a;
    --photo-b:#c9c6c0;
  }
  *{box-sizing:border-box;margin:0;padding:0}
  html,body{width:1200px;height:775px;overflow:hidden;background:var(--white)}
  body{position:relative;font-family:"Open Sans",Arial,sans-serif}

  .site-header{position:absolute;left:0;top:0;width:1200px;height:91px;background:var(--black);color:var(--white)}
  .menu-toggle{position:absolute;left:131px;top:40px;display:flex;align-items:center;gap:8px;font:500 15px "Montserrat",Arial,sans-serif;letter-spacing:.2px}
  .brand{position:absolute;left:0;right:0;top:30px;text-align:center;font:500 26px "Montserrat",Arial,sans-serif;letter-spacing:.5px}
  .auth-btn{position:absolute;top:31px;width:87px;height:33px;border:2px solid var(--white);display:flex;align-items:center;justify-content:center;font:500 14px "Montserrat",Arial,sans-serif}
  .auth-btn.login{left:868px}
  .auth-btn.signup{left:972px}

  .mission-title{position:absolute;left:117px;top:148px;font:500 21px "Montserrat",Arial,sans-serif;color:var(--black)}

  .tabs{position:absolute;left:114px;top:204px;display:flex}
  .tab{width:157px;height:39px;display:flex;align-items:center;justify-content:center;font:500 16px "Montserrat",Arial,sans-serif;background:var(--tab-grey);border:1px solid var(--tab-border);color:var(--black)}
  .tab.active{background:var(--accent);border-color:var(--accent);color:var(--white)}

  .timeline-line{position:absolute;left:126px;top:297px;width:5px;height:347px;background:var(--timeline)}
  .timeline-dot{position:absolute;left:118px;width:21px;height:21px;border-radius:50%;background:var(--timeline)}
  .timeline-dot.current{background:var(--accent)}

  .story-text{position:absolute;width:590px;font-size:11.5px;line-height:18px;color:var(--text-body)}
  .story-photo{position:absolute;left:157px;top:423px;width:560px;height:126px;background:linear-gradient(90deg,var(--photo-b),var(--photo-a) 35%,var(--photo-b) 60%,var(--photo-a))}

  .share-icons{position:absolute;left:893px;top:132px;display:flex;gap:22px;align-items:center}
  .share-icon{width:22px;height:22px;border-radius:50%;background:var(--icon-grey)}
  .share-icon.book{width:32px;height:22px;border-radius:2px;background:none;border:2px solid var(--icon-grey)}

  .mission-card{position:absolute;left:766px;top:167px;width:293px;height:523px;background:var(--accent);color:var(--white)}
  .mission-card > *{position:absolute}
  .card-name{left:28px;top:32px;font:500 19px "Montserrat",Arial,sans-serif;color:var(--black)}
  .card-location{left:28px;top:68px;display:flex;align-items:center;gap:7px;font-size:15px}
  .card-org{left:28px;top:96px;font-size:15px}
  .support-row{left:28px;top:148px;width:253px;height:29px;border-bottom:1px solid rgba(255,255,255,.6);display:flex;align-items:flex-start;gap:12px;font-size:15px}
  .supporters{display:flex;gap:7px;margin-top:2px}
  .support-row .chevron{margin-left:auto;margin-top:6px}
  .support-note{left:30px;top:188px;font-size:12px;font-weight:600}
  .progress{left:28px;top:217px}
  .progress-value{position:absolute;left:0;top:0;width:94px;height:94px;display:flex;align-items:center;justify-content:center;font:400 22px "Open Sans",Arial,sans-serif}
  .funding-facts{left:134px;top:227px;font-size:12px;font-weight:600;line-height:21px}
  .funding-facts .need{display:flex;align-items:center;gap:6px}
  .participate-label{left:40px;top:316px;font-size:16px}
  .options{left:26px;top:349px;width:253px;list-style:none}
  .option{height:29px;background:var(--accent-dark);border-bottom:1px solid var(--accent);display:flex;align-items:center;padding:0 12px;font-size:12px;font-weight:600}
  .option .check{width:14px;height:14px;background:var(--white);border-radius:2px;margin-right:21px}
  .option .cart{margin-left:auto}

  .site-footer{position:absolute;left:0;top:728px;width:1200px;height:47px;background:var(--footer);color:var(--white);display:flex;align-items:center;justify-content:center;font-size:12.5px}
</style>
</head>
<body>

<header class="site-header">
  <div class="menu-toggle">
    <svg width="30" height="16" viewBox="0 0 30 16"><rect y="0" width="30" height="3" rx="1.5" fill="#fff"/><rect y="6.5" width="30" height="3" rx="1.5" fill="#fff"/><rect y="13" width="30" height="3" rx="1.5" fill="#fff"/></svg>
    <span>SEE THE MISSIONS</span>
    <svg width="17" height="17" viewBox="0 0 17 17"><circle cx="7" cy="7" r="5" fill="none" stroke="#9a9a9a" stroke-width="2.4"/><line x1="10.5" y1="10.5" x2="15.5" y2="15.5" stroke="#9a9a9a" stroke-width="2.8" stroke-linecap="round"/></svg>
  </div>
  <div class="brand">HOPEWINGSRALLY</div>
  <a class="auth-btn login">LOGIN</a>
  <a class="auth-btn signup">SIGN UP</a>
</header>

<h1 class="mission-title">Mission: Orphan Maria, 11y</h1>

<nav class="tabs">
  <div class="tab active">Story</div>
  <div class="tab">Updates</div>
  <div class="tab">Comments</div>
</nav>

<div class="timeline-line"></div>
<div class="timeline-dot" style="top:287px"></div>
<div class="timeline-dot current" style="top:465px"></div>
<div class="timeline-dot" style="top:634px"></div>

<p class="story-text" style="left:153px;top:283px">Morbi porta libero id ullamcorper nonummy nibh ligula pulvinar metus eget consectetuer augue nisi quis lacus Ut ac mi quis lacus mollis aliquam Curabitur iaculis tempus eros Curabitur vel mi sit amet magna malesuada ultrices Ut nisi erat fermentum vel congue id euismod in elit</p>
<p class="story-text" style="left:153px;top:352px">Fusce ultricies orci ac feugiat suscipit leo massa sodales velit et scelerisque mi tortor at ipsum cligula augue bibendum accumsan vestibulum ut commodo a mi Morbi ornare gravida elit Integer congue augue et malesuada iaculis ipsum dui aliquet felis at cursus magna nisl nec elit Praesent elemen</p>
<div class="story-photo" role="img" aria-label="Photo of a smiling couple on a sofa looking at a laptop"></div>
<p class="story-text" style="left:157px;top:566px">Morbi porta libero id ullamcorper nonummy nibh ligula pulvinar metus eget consectetuer augue nisi quis lacus Ut ac mi quis lacus mollis aliquam Curabitur iaculis tempus eros Curabitur vel mi sit amet magna malesuada ultrices Ut nisi erat fermentum vel congue id euismod in elit</p>
<p class="story-text" style="left:157px;top:635px">Fusce ultricies orci ac feugiat suscipit leo massa sodales velit et scelerisque mi tortor at ipsum cligula augue bibendum accumsan vestibulum ut commodo a mi Morbi ornare gravida elit Inte</p>

<div class="share-icons">
  <span class="share-icon book"></span>
  <span class="share-icon"></span>
  <span class="share-icon"></span>
  <span class="share-icon"></span>
</div>

<aside class="mission-card">
  <div class="card-name">Name: Maria, 11y</div>
  <div class="card-location">
    <svg width="13" height="18" viewBox="0 0 13 18"><path d="M6.5 0C2.9 0 0 2.8 0 6.4 0 11 6.5 18 6.5 18S13 11 13 6.4C13 2.8 10.1 0 6.5 0z" fill="#000"/><circle cx="6.5" cy="6.3" r="2.4" fill="#ffb400"/></svg>
    <span>Kalkutta</span>
  </div>
  <div class="card-org">Organization: Jacob</div>

  <div class="support-row">
    <span>Support</span>
    <span class="supporters">
      <svg width="19" height="19" viewBox="0 0 19 19"><circle cx="9.5" cy="5" r="4.5"/><path d="M0 19c0-5 3.5-8 9.5-8s9.5 3 9.5 8z"/></svg>
      <svg width="19" height="19" viewBox="0 0 19 19"><circle cx="9.5" cy="5" r="4.5"/><path d="M0 19c0-5 3.5-8 9.5-8s9.5 3 9.5 8z"/></svg>
      <svg width="19" height="19" viewBox="0 0 19 19"><circle cx="9.5" cy="5" r="4.5"/><path d="M0 19c0-5 3.5-8 9.5-8s9.5 3 9.5 8z"/></svg>
      <svg width="19" height="19" viewBox="0 0 19 19"><circle cx="9.5" cy="5" r="4.5"/><path d="M0 19c0-5 3.5-8 9.5-8s9.5 3 9.5 8z"/></svg>
      <svg width="19" height="19" viewBox="0 0 19 19"><circle cx="9.5" cy="5" r="4.5"/><path d="M0 19c0-5 3.5-8 9.5-8s9.5 3 9.5 8z"/></svg>
      <svg width="19" height="19" viewBox="0 0 19 19"><circle cx="9.5" cy="5" r="4.5"/><path d="M0 19c0-5 3.5-8 9.5-8s9.5 3 9.5 8z"/></svg>
    </span>
    <svg class="chevron" width="8" height="12" viewBox="0 0 8 12"><path d="M1.5 1l5 5-5 5" fill="none" stroke="#fff" stroke-width="1.6"/></svg>
  </div>
  <div class="support-note">My support is now: $5/month</div>

  <div class="progress">
    <svg width="94" height="94" viewBox="0 0 94 94">
      <circle cx="47" cy="47" r="43" fill="none" stroke="#fff" stroke-width="4"/>
      <circle cx="47" cy="47" r="43" fill="none" stroke="#000" stroke-width="5" stroke-dasharray="121.6 270.2" transform="rotate(-90 47 47)"/>
    </svg>
    <div class="progress-value">45%</div>
  </div>
  <div class="funding-facts">
    <div>$15 given</div>
    <div>of total$35 needed</div>
    <div class="need">
      <svg width="15" height="15" viewBox="0 0 15 15"><rect x="0.7" y="2" width="13.6" height="12.3" fill="none" stroke="#000" stroke-width="1.3"/><rect x="0.7" y="2" width="13.6" height="3" fill="#000"/><g fill="#000"><rect x="3" y="7" width="2" height="2"/><rect x="6.5" y="7" width="2" height="2"/><rect x="10" y="7" width="2" height="2"/><rect x="3" y="10.5" width="2" height="2"/><rect x="6.5" y="10.5" width="2" height="2"/><rect x="10" y="10.5" width="2" height="2"/></g></svg>
      <span>Per month need</span>
    </div>
  </div>

  <div class="participate-label">Participate</div>
  <ul class="options">
    <li class="option"><span class="check"></span>I am in, $1/ month<svg class="cart" width="20" height="17" viewBox="0 0 20 17"><path d="M0 1h3.5l2.5 10h11l2-7H5" fill="none" stroke="#000" stroke-width="1.5"/><path d="M6 6.5h11M6.6 9h10" stroke="#000" stroke-width="1"/><circle cx="7.5" cy="14.5" r="1.6"/><circle cx="15.5" cy="14.5" r="1.6"/></svg></li>
    <li class="option"><span class="check"></span>Increased, $5 / month<svg class="cart" width="20" height="17" viewBox="0 0 20 17"><path d="M0 1h3.5l2.5 10h11l2-7H5" fill="none" stroke="#000" stroke-width="1.5"/><path d="M6 6.5h11M6.6 9h10" stroke="#000" stroke-width="1"/><circle cx="7.5" cy="14.5" r="1.6"/><circle cx="15.5" cy="14.5" r="1.6"/></svg></li>
    <li class="option"><span class="check"></span>Decent help, $10 / month<svg class="cart" width="20" height="17" viewBox="0 0 20 17"><path d="M0 1h3.5l2.5 10h11l2-7H5" fill="none" stroke="#000" stroke-width="1.5"/><path d="M6 6.5h11M6.6 9h10" stroke="#000" stroke-width="1"/><circle cx="7.5" cy="14.5" r="1.6"/><circle cx="15.5" cy="14.5" r="1.6"/></svg></li>
    <li class="option"><span class="check"></span>Whole Kid, $35/month<svg class="cart" width="20" height="17" viewBox="0 0 20 17"><path d="M0 1h3.5l2.5 10h11l2-7H5" fill="none" stroke="#000" stroke-width="1.5"/><path d="M6 6.5h11M6.6 9h10" stroke="#000" stroke-width="1"/><circle cx="7.5" cy="14.5" r="1.6"/><circle cx="15.5" cy="14.5" r="1.6"/></svg></li>
    <li class="option"><span class="check"></span>My amount<svg class="cart" width="20" height="17" viewBox="0 0 20 17"><path d="M0 1h3.5l2.5 10h11l2-7H5" fill="none" stroke="#000" stroke-width="1.5"/><path d="M6 6.5h11M6.6 9h10" stroke="#000" stroke-width="1"/><circle cx="7.5" cy="14.5" r="1.6"/><circle cx="15.5" cy="14.5" r="1.6"/></svg></li>
  </ul>
</aside>

<footer class="site-footer">© 2016 Company Name&nbsp; All right reserved&nbsp; Term of Use</footer>

</body>
</html>
```